Tuition Center Website

We need a new web site for a tutoring company based in sydney.

We only teach senior highschool students and pride ourselves on building the students abilities to think their way through life.

I would like a bright and vibrant website that looks professional and modern.
It needs to look simple and neat but also have the functionality we need.
Images and flash would be good.

Please keep in mind that the site must be appealing to a younger audience.

We need a multipage website with the following navigation bars:

1.Home (As logo not "home" button)
I would like a news box/ticker somewhere that can stream our chatterbook and pipstream feeds and also any news updates we want to put up.
Subscribe to newsletter button.

2. About us.
This needs to be a pull down into:
-What we do
-Why we do it
-How we do it

3. Courses
Pulldown into:
-Maths
-English
-Science
(we may need to attach extra pages behind these e.g. Courses/Science/Physics or Courses/Science/Chemistry and possibly add a link to a new zandlo form)

4. Inspired
This page is like a blog page where we can upload videos, links to articles that we find to be inspiring and hopefully will inspire others.

5. Inspire
This is a recruitment page. Only content here.

6. Contact us.
Mapquill map widget and a 'contact us' form

* Our branding requires green close to #12FF3D

***Please have a look at the current website.
@ www.velmorlearning.com.au

Thanks everybody hope the revision of my brief is better and more informative than my last one

Target Market(s)

senior highschool students aged 15-19, parents ( to a lesser degree)

Industry/Entity Type

It Company

Requirements
Must have
• Ability to change content on pages.

The green doesn't have to be everywhere, but it must be obvious that it is our colour.

Nice to have
• Sites with a nicer mix of images and flash will be given more consideration. But then again, if you amaze us, you amaze us and we will go with your design.
Should not have
• Should stay away from ocre, brown colours and serif fonts.

```html
<!DOCTYPE html>
<html lang="en">
<head>
<meta charset="utf-8">
<title>Velmor Learning – Real HSC Coaching & Mentoring</title>
<link rel="stylesheet" href="https://fonts.googleapis.com/css2?family=Source+Sans+3:ital,wght@0,300;0,400;0,600;1,300&display=swap">
<style>
:root{
  --green:#5fb31a;
  --green-bright:#7ed321;
  --green-dark:#4e8a16;
  --green-text:#6b961e;
  --date:#9aac7a;
  --hero-top:#62991a;
  --hero-bottom:#93c43c;
  --nav-top:#3a3a3a;
  --nav-bottom:#1e1e1e;
  --ink:#2b2b2b;
  --body:#6a6a6a;
  --footer:#2a2a2a;
  --orange:#f39c12;
  --white:#ffffff;
}
*{margin:0;padding:0;box-sizing:border-box}
h1,h2,h3{font-weight:400}
html,body{width:1155px;height:1200px;overflow:hidden;background:var(--white)}
body{position:relative;font-family:"Source Sans 3",sans-serif;color:var(--ink)}
a{color:inherit;text-decoration:none}

.utility-links{position:absolute;top:11px;right:109px;font-size:13px;color:#777;font-weight:300}
.utility-links span{margin:0 5px;color:#aaa}

.brand{position:absolute;left:122px;top:42px}
.brand-name{font-size:40px;font-weight:600;color:var(--green);line-height:1}
.brand-tagline{font-size:15px;color:#444;margin-top:4px;font-weight:400}

.search{position:absolute;left:813px;top:70px;width:229px;height:30px;border:1px solid #ddd;display:flex;align-items:center;padding:0 10px;font-size:11px;font-style:italic;color:#999;font-weight:300}
.search svg{position:absolute;right:10px;top:7px}

.main-nav{position:absolute;left:0;top:123px;width:1155px;height:53px;background:linear-gradient(var(--nav-top),var(--nav-bottom));display:flex;padding-left:112px}
.main-nav a{color:#eee;font-size:17px;line-height:53px;padding:0 16px;border-left:1px solid #4a4a4a}
.main-nav a:first-child{border-left:0}

.hero{position:absolute;left:0;top:176px;width:1155px;height:395px;background:linear-gradient(var(--hero-top),var(--hero-bottom))}
.hero-copy{position:absolute;left:122px;top:44px;color:var(--white);width:340px}
.hero-title{font-size:47px;line-height:1;font-weight:600}
.hero-sub{font-size:24px;font-weight:300;margin-top:6px}
.hero-text{font-size:14px;font-weight:300;line-height:23px;margin-top:10px}
.enquire{position:absolute;left:122px;top:257px;width:121px;height:33px;background:var(--green-dark);border:1px solid #8fc24d;color:var(--white);font-size:15px;font-weight:600;text-align:center;line-height:31px}
.slide-dots{position:absolute;left:125px;top:321px;display:flex;gap:3px}
.slide-dots i{width:10px;height:10px;border-radius:50%;background:rgba(255,255,255,.5)}
.slide-dots i:first-child{background:var(--white)}
.slide-frame{position:absolute;left:510px;top:29px;width:525px;height:323px;background:#e9f0df;padding:7px}
.slide-art{width:100%;height:100%;background:linear-gradient(#ffffff,#f4f8ee)}
.slide-arrow{position:absolute;top:162px;width:28px;height:44px;background:var(--green-bright)}
.slide-arrow.prev{left:510px;border-radius:0 22px 22px 0}
.slide-arrow.next{left:1007px;border-radius:22px 0 0 22px}

.section-title{position:absolute;font-size:23px;color:var(--ink)}

.post{position:absolute;left:114px;width:360px}
.post-title{font-size:15.5px;color:var(--green-text)}
.post-date{font-size:13px;color:var(--date);font-weight:300;margin-top:1px}
.post-text{font-size:13.5px;color:var(--body);font-weight:300;line-height:20px;margin-top:6px}

.testimonial{position:absolute;width:260px}
.quote-mark{position:absolute;left:0;top:-6px;font-size:34px;font-weight:600;color:#555}
.avatar{position:absolute;left:22px;top:0;width:80px;height:70px;border:1px solid #ddd;background:linear-gradient(#e8e0d8,#c7b2a0)}
.testimonial-lead{position:absolute;left:110px;top:-2px;width:150px;font-size:12px;font-style:italic;color:#777;font-weight:300;line-height:18px}
.testimonial-rest{position:absolute;left:22px;top:84px;width:238px;font-size:12px;font-style:italic;color:#777;font-weight:300;line-height:18px}
.testimonial-author{position:absolute;left:23px;top:129px;font-size:13px;color:#777}

.trial-card{position:absolute;left:798px;top:658px;width:252px;height:143px;background:linear-gradient(135deg,#b9a27a,#7c6a52 55%,#4e5f6c)}
.trial-card svg{position:absolute;left:0;top:0}
.trial-text{position:absolute;left:799px;top:808px;width:255px;font-size:13.5px;color:var(--body);font-weight:300;line-height:18px}

.news-list{position:absolute;left:800px;top:910px;list-style:none}
.news-list li{font-size:12.5px;color:#333;line-height:23px;padding-left:14px;position:relative}
.news-list li::before{content:"";position:absolute;left:0;top:8px;border-left:5px solid #999;border-top:4px solid transparent;border-bottom:4px solid transparent}

.footer{position:absolute;left:0;top:1065px;width:1155px;height:135px;background:var(--footer);border-top:5px solid #151515}
.footer-links{position:absolute;left:120px;top:32px;font-size:13.5px;color:#ddd;font-weight:300}
.footer-links span{margin:0 5px;color:#888}
.copyright{position:absolute;left:120px;top:68px;font-size:13px;color:#ddd;font-weight:300}
.social{position:absolute;right:110px;top:32px;display:flex;gap:12px;font-size:12.5px;color:#ddd}
.social a{display:flex;align-items:center;gap:5px}
.social a::before{content:"";width:10px;height:10px;border-radius:50%;background:#eee}
</style>
</head>
<body>

<nav class="utility-links">
  <a href="#">BSE Past HSC Papers</a><span>|</span><a href="#">State Students Online</a><span>|</span><a href="#">Uniadmit</a><span>|</span><a href="#">Senior Exams online</a><span>|</span><a href="#">Help</a><span>|</span><a href="#">Velmor on Chatterbook</a>
</nav>

<header class="brand">
  <div class="brand-name">Velmor Learning</div>
  <div class="brand-tagline">clear thinking for senior students</div>
</header>

<div class="search">Search here..
  <svg width="16" height="16" viewBox="0 0 16 16"><circle cx="6.5" cy="6.5" r="5" fill="none" stroke="#999" stroke-width="2"/><line x1="10" y1="10" x2="15" y2="15" stroke="#999" stroke-width="2.5"/></svg>
</div>

<nav class="main-nav">
  <a href="#">Home</a><a href="#">About Us</a><a href="#">Find Us</a><a href="#">Get in Touch</a><a href="#">Recent News</a><a href="#">Year 10 Classes</a><a href="#">Yr 11 &amp; 12 HSC Classes</a>
</nav>

<section class="hero">
  <div class="hero-copy">
    <h1 class="hero-title">I am Velmor..</h1>
    <p class="hero-sub">Real HSC Coaching &amp; Mentoring</p>
    <p class="hero-text">The HSC help you need, in the years you need it. We offer small classes, individualised attention and genuine care for each student. It's different - in a good way. Feel free to find out more about us, and let us know if there's any way we can help you on your journey.</p>
  </div>
  <a class="enquire" href="#">ENQIRE NOW</a>
  <div class="slide-dots"><i></i><i></i><i></i><i></i></div>
  <div class="slide-frame"><div class="slide-art" role="img" aria-label="Line illustration of school supplies: bag, pencils, laptop, chalkboard, flasks, books"></div></div>
  <a class="slide-arrow prev" href="#" aria-label="Previous slide"><svg width="28" height="44" viewBox="0 0 28 44"><path d="M15 17 L9 22 L15 27Z" fill="#fff"/></svg></a>
  <a class="slide-arrow next" href="#" aria-label="Next slide"><svg width="28" height="44" viewBox="0 0 28 44"><path d="M13 17 L19 22 L13 27Z" fill="#fff"/></svg></a>
</section>

<h2 class="section-title" style="left:112px;top:619px">Recent Blog Posts</h2>
<article class="post" style="top:660px">
  <h3 class="post-title">Mauris vel lacus vitae felis vestibulum</h3>
  <p class="post-date">20 March 2013</p>
  <p class="post-text">Duis tincidunt lectus quis dui viverra vestibulum. Suspendisse vulputate aliquam dui. Nulla elementum dui ut augue. Phasellus felis dolor, scelerisque a, tempus eget, lobortis id, libero.</p>
</article>
<article class="post" style="top:791px">
  <h3 class="post-title">Fusce ultricies orci ac feugiat s</h3>
  <p class="post-date">20 March 2013</p>
  <p class="post-text">Duis tincidunt lectus quis dui viverra vestibulum. Suspendisse vulputate aliquam dui. Nulla elementum dui ut augue.</p>
</article>
<article class="post" style="top:899px">
  <h3 class="post-title">Fusce ultricies orci ac feugiat s</h3>
  <p class="post-date">20 March 2013</p>
  <p class="post-text">Lorem ipsum dolor sit amet, consectetuer adipiscing elit. Nam cursus. Morbi ut mi. Nullam enim leo, egestas id, condimentum at, laoreet mattis, massa.</p>
</article>

<h2 class="section-title" style="left:508px;top:619px">What Our Student Say</h2>
<div class="testimonial" style="left:503px;top:666px">
  <span class="quote-mark">“</span>
  <div class="avatar" role="img" aria-label="Portrait of a smiling male student"></div>
  <p class="testimonial-lead">Nunc tempus felis vitae urna. Vivamus porttitor, neque at volutpat rutrum, purus nisi eleifend libero, a tempus</p>
  <p class="testimonial-rest">Morbi eget arcu. Morbi porta, libero id ullamcor-per nonummy, nibh ligula pulvinar metus ”</p>
  <p class="testimonial-author">By Author Name</p>
</div>
<div class="testimonial" style="left:509px;top:831px">
  <span class="quote-mark">“</span>
  <div class="avatar" role="img" aria-label="Portrait of a thoughtful female student"></div>
  <p class="testimonial-lead">Nunc tempus felis vitae urna. Vivamus porttitor, neque at volutpat rutrum, purus nisi eleifend libero, a tempus</p>
  <p class="testimonial-rest">Morbi eget arcu. Morbi porta, libero id ullamcor-per nonummy, nibh ligula pulvinar metus ”</p>
  <p class="testimonial-author">By Author Name</p>
</div>

<h2 class="section-title" style="left:798px;top:619px">Ask for your free trial lesson</h2>
<a class="trial-card" href="#" role="img" aria-label="Student studying in a library, with a Free Trail Now banner">
  <svg width="252" height="143" viewBox="0 0 252 143">
    <polygon points="0,143 0,125 252,88 252,143" fill="var(--orange)"/>
    <text x="118" y="131" transform="rotate(-9 118 131)" fill="#fff" font-family="Source Sans 3, sans-serif" font-size="21" font-weight="600">Free Trail Now</text>
  </svg>
</a>
<p class="trial-text">Because we believe you shouldn't have to sign up until you see what it's actually like.</p>

<h2 class="section-title" style="left:797px;top:871px">Recent News</h2>
<ul class="news-list">
  <li>Year 11 FREE HSC Workshops!</li>
  <li>Uni Open Days 2012</li>
  <li>Considering Studying Interstate?</li>
</ul>

<footer class="footer">
  <nav class="footer-links">
    <a href="#">Home</a><span>|</span><a href="#">About Us</a><span>|</span><a href="#">Find Us</a><span>|</span><a href="#">Get in Touch</a><span>|</span><a href="#">Recent News</a><span>|</span><a href="#">Year 10 Classes</a><span>|</span><a href="#">Yr 11 &amp; 12 HSC Classes</a>
  </nav>
  <p class="copyright">© 2013 Company Name.&nbsp; All right reserved.&nbsp; Term of Use</p>
  <nav class="social">
    <a href="#">chatterbook</a><a href="#">pipstream</a><a href="#">linkwell</a><a href="#">snapgrove</a>
  </nav>
</footer>

</body>
</html>
```